Harbor Lanterns Remember

The song is an instrumental song that was built around a slide show with an original poem, "Carry the Ember". I would like to do an Melvo digital booklet if possible.

The general vision for the album cover/possible Melvo digital booklet is a person coming from a dark place and just seeing a glimpse of light (representing hope of a better day).

Stills from the movie attached for reference.

Watch the movie on Vidra .... http://vidra.cx/Kq4pWmTz2Ha

```html
<!DOCTYPE html>
<html lang="en">
<head>
<meta charset="utf-8">
<title>Carry the Ember</title>
<link rel="stylesheet" href="https://fonts.googleapis.com/css2?family=Kaushan+Script&family=Oswald:wght@600;700&display=swap">
<style>
  :root {
    --night: #000000;
    --ember: #c5512f;
    --ember-deep: #d4441c;
    --glow-white: #fffdf6;
    --glow-amber: #f4a066;
    --glow-rust: #8a2f14;
    --ink-light: #ffffff;
  }
  html, body {
    margin: 0;
    padding: 0;
    background: var(--night);
    overflow: hidden;
  }
  .cover {
    position: relative;
    width: 1200px;
    height: 1200px;
    background: var(--night);
    overflow: hidden;
  }
  .cover__title {
    position: absolute;
    top: 92px;
    left: 0;
    width: 1200px;
    margin: 0;
    text-align: center;
    font-family: "Kaushan Script", cursive;
    font-weight: 400;
    font-size: 92px;
    line-height: 1.1;
    letter-spacing: 6px;
    background: linear-gradient(180deg, var(--glow-white) 15%, var(--glow-amber) 55%, var(--ember-deep) 95%);
    -webkit-background-clip: text;
    background-clip: text;
    color: transparent;
  }
  .cover__tunnel {
    position: absolute;
    left: 240px;
    top: 220px;
    width: 720px;
    height: 720px;
  }
  .cover__credit {
    position: absolute;
    right: 26px;
    bottom: 14px;
    text-align: right;
    font-family: "Oswald", sans-serif;
    text-transform: uppercase;
    line-height: 1;
  }
  .cover__credit-lead {
    display: block;
    color: var(--ink-light);
    font-weight: 600;
    font-size: 40px;
    letter-spacing: -0.5px;
    margin-right: 30px;
    transform: scaleX(0.85);
    transform-origin: right;
  }
  .cover__credit-name {
    display: block;
    color: var(--ember);
    font-weight: 700;
    font-size: 72px;
    letter-spacing: -1px;
    margin-top: 6px;
    transform: scaleX(0.85);
    transform-origin: right;
  }
</style>
</head>
<body>
  <main class="cover">
    <h1 class="cover__title">Carry the Ember</h1>

    <svg class="cover__tunnel" viewBox="0 0 720 720" role="img" aria-label="Photograph of a dark brick tunnel with bright light glowing at its far end">
      <defs>
        <radialGradient id="tunnelGlow" cx="50%" cy="36%" r="55%" fx="50%" fy="34%">
          <stop offset="0%" stop-color="var(--glow-white)"/>
          <stop offset="16%" stop-color="var(--glow-white)"/>
          <stop offset="26%" stop-color="var(--glow-amber)"/>
          <stop offset="45%" stop-color="var(--glow-rust)" stop-opacity="0.6"/>
          <stop offset="75%" stop-color="var(--night)" stop-opacity="0"/>
        </radialGradient>
      </defs>
      <rect width="720" height="720" fill="url(#tunnelGlow)"/>
    </svg>

    <p class="cover__credit">
      <span class="cover__credit-lead">An original poem by</span>
      <span class="cover__credit-name">Dario Vellucci</span>
    </p>
  </main>
</body>
</html>
```